Business Cards for new orthopaedic surgery practice

My husband and I are starting our own orthopaedic surgery practice. We are looking for a business card that is uniform, but one will have my name/title and the other will have his. You can just create one design with my name on it for now. But when I choose your design as the winning design I will ask that you add another copy with his name/title.

We are looking for classy, simple, elite all in one. We like dark blues/a little gold/yellow. Something that goes with our logo. We want our logo incorporated. Here is all the info you need:
Business name: RV Bone & Vitality Center
Location: 38517 North Willowmere Ave
Ashford Glen, FL 33990
Phone: 954-218-4063
Fax: 954-582-7341
Email: info@myrvbonecare.example

Names: Lydia Vance, M.D.
Board Certified Hand and Upper Extremity Surgeon

Ebo Dansu, M.D.
Board Certified Hip & Knee Replacement/General Orthopaedic Surgeon

Can decide what you want to put on the back. Maybe a slogan:
Rooted in Care. Focused on You

I am just going to upload our logo. The only thing is if we select you as the winning design, the location, and phone numbers may change. We will need your help to update that once fully solidified.

Industry/Entity Type

Medical

Contact Information for Business Card

Colors
0054AA
0677BA
7BADD7
CADEEF
E8F1F8
0094D4
00A9DD
6FCCEA
C7EBF8
E9F6FB

Requirements
Must have
• class, appeal,
Should not have
• We want to air on the side of masculine if we are looking at masculine vs. feminine feel. But we still want it classy, sophisticated, and something we will love

```html
<!DOCTYPE html>
<html lang="en">
<head>
<meta charset="utf-8">
<title>RV Bone &amp; Vitality Center – Business Card</title>
<link rel="stylesheet" href="https://fonts.googleapis.com/css2?family=Nunito:wght@400;600;700&display=swap">
<style>
  :root {
    --stage: #7f7f7f;
    --paper: #f5f5f7;
    --white: #ffffff;
    --navy: #2e3a8c;
    --sky: #6ebee0;
    --mid-blue: #529cc8;
    --deep-blue: #2b73a0;
  }
  * { margin: 0; padding: 0; box-sizing: border-box; }
  html, body { width: 1200px; height: 1200px; overflow: hidden; }
  body {
    background: var(--stage);
    font-family: "Nunito", sans-serif;
    position: relative;
  }
  .card {
    position: absolute;
    left: 223px;
    width: 1047px;
    height: 590px;
    border-radius: 42px;
    overflow: hidden;
    background: var(--paper);
    transform: scale(0.72);
    transform-origin: top left;
  }
  .card-front { top: 148px; }
  .card-back { top: 625px; }
  .card-art { position: absolute; inset: 0; width: 100%; height: 100%; }

  .brand-lockup {
    position: absolute;
    left: 0; right: 0;
    top: 262px;
    display: flex;
    align-items: center;
    justify-content: center;
    gap: 16px;
  }
  .brand-dot {
    width: 22px; height: 22px;
    border-radius: 50%;
    background: var(--navy);
  }
  .brand-name {
    font-weight: 700;
    font-size: 44px;
    color: var(--navy);
    letter-spacing: 0.5px;
  }

  .doctor-name {
    position: absolute;
    left: 85px; top: 70px;
    font-weight: 700;
    font-size: 31px;
    color: var(--sky);
    letter-spacing: 0.3px;
  }
  .doctor-title {
    position: absolute;
    left: 84px; top: 116px;
    font-size: 23px;
    color: var(--navy);
  }
  .divider {
    position: absolute;
    left: 311px; top: 208px;
    width: 51px; height: 2px;
    background: var(--navy);
  }
  .contact-list { list-style: none; position: absolute; left: 78px; top: 262px; }
  .contact-item {
    display: flex;
    align-items: flex-start;
    gap: 24px;
    font-size: 20px;
    color: var(--navy);
    line-height: 25px;
    margin-bottom: 32px;
  }
  .contact-item:nth-child(3) { margin-bottom: 34px; }
  .contact-icon { width: 38px; height: 38px; flex: none; margin-top: -6px; }
  .panel-brand {
    position: absolute;
    left: 835px; top: 48px;
    width: 192px;
    text-align: center;
    font-weight: 700;
    font-size: 28px;
    line-height: 34px;
    color: var(--white);
  }
</style>
</head>
<body>

<section class="card card-front" aria-label="Card front">
  <svg class="card-art" viewBox="0 0 1047 590" aria-hidden="true">
    <rect x="0" y="0" width="1047" height="81" fill="var(--sky)"/>
    <polygon points="650,81 760,0 1047,0 1047,81" fill="var(--mid-blue)"/>
    <polygon points="775,81 890,0 1047,0 1047,81" fill="var(--deep-blue)"/>
    <rect x="0" y="81" width="1047" height="12" fill="var(--white)"/>
    <rect x="0" y="494" width="1047" height="12" fill="var(--white)"/>
    <rect x="0" y="506" width="1047" height="84" fill="var(--sky)"/>
    <polygon points="0,506 410,506 295,590 0,590" fill="var(--mid-blue)"/>
    <polygon points="0,506 285,506 165,590 0,590" fill="var(--deep-blue)"/>
  </svg>
  <div class="brand-lockup">
    <span class="brand-dot"></span>
    <span class="brand-name">RV Bone &amp; Vitality Center</span>
  </div>
</section>

<section class="card card-back" aria-label="Card back">
  <svg class="card-art" viewBox="0 0 1047 590" aria-hidden="true">
    <rect x="802" y="0" width="13" height="590" fill="var(--white)"/>
    <rect x="815" y="0" width="232" height="590" fill="var(--sky)"/>
    <polygon points="815,0 1047,0 1047,492 815,315" fill="var(--mid-blue)"/>
    <polygon points="815,0 1047,0 1047,337 815,155" fill="var(--deep-blue)"/>
  </svg>

  <h1 class="doctor-name">LYDIA VANCE, M.D.</h1>
  <p class="doctor-title">Board Certified Hand and Upper Extremity Surgeon</p>
  <div class="divider"></div>

  <ul class="contact-list">
    <li class="contact-item">
      <svg class="contact-icon" viewBox="0 0 24 24" fill="none" stroke="var(--navy)" stroke-width="1.4" stroke-linejoin="round" aria-hidden="true">
        <path d="M5 3h3l1.5 4-2 1.5a11 11 0 0 0 8 8L17 14.5l4 1.5v3a2 2 0 0 1-2 2A16 16 0 0 1 3 5a2 2 0 0 1 2-2z"/>
      </svg>
      <span>954-218-4063</span>
    </li>
    <li class="contact-item">
      <svg class="contact-icon" viewBox="0 0 24 24" fill="none" stroke="var(--navy)" stroke-width="1.6" stroke-linejoin="round" aria-hidden="true">
        <path d="M7 8V3h10v5"/>
        <rect x="3" y="8" width="18" height="8" rx="1.5"/>
        <rect x="7" y="13" width="10" height="8"/>
      </svg>
      <span>954-582-7341</span>
    </li>
    <li class="contact-item">
      <svg class="contact-icon" viewBox="0 0 24 24" fill="none" stroke="var(--navy)" stroke-width="1.5" stroke-linejoin="round" aria-hidden="true">
        <rect x="3" y="6" width="18" height="13"/>
        <path d="M3 6l9 7 9-7"/>
      </svg>
      <span>info@myrvbonecare.example</span>
    </li>
    <li class="contact-item">
      <svg class="contact-icon" viewBox="0 0 24 24" fill="none" stroke="var(--navy)" stroke-width="1.5" stroke-linejoin="round" aria-hidden="true">
        <path d="M4 21V10l8-6 8 6v11h-5v-7H9v7z"/>
      </svg>
      <span>38517 North Willowmere Ave<br>Ashford Glen, FL 33990</span>
    </li>
  </ul>

  <p class="panel-brand">RV Bone &amp; Vitality Center</p>
</section>

</body>
</html>
```